Property Developer Business card design

we need a business card design + printing for a new Property developer company based in melbourne.
We are a group of investors investing in a property developer business. We have more projects involved in residential property as opposed to commercial property but we are involved in both market. we also provide consulting services with overseas investors willing to invest in the australian property market.
Updates
I have uploaded the logo. I'm not very convince with the colors of my logo... any suggestion please?.
Thanks guys!
Target Market(s)
property investors or person willing to purchase investment property
Industry/Entity Type
Residential
Contact Information for Business Card
Bramblecourt Holdings Australia Pty Ltd
Look and feel

```html
<!DOCTYPE html>
<html lang="en">
<head>
<meta charset="utf-8">
<title>Bramblecourt Holdings Australia – Business Card</title>
<link rel="stylesheet" href="https://fonts.googleapis.com/css2?family=Tinos:wght@400&display=swap">
<style>
  :root {
    --backdrop: #2a2a2a;
    --brand-blue: #0b7ac4;
    --brand-red: #b01c24;
    --address-red: #7a1a14;
    --ink: #1c1c1c;
    --paper: #ffffff;
    --icon-blue: #1a78c2;
  }
  * { margin: 0; padding: 0; box-sizing: border-box; }
  html, body { width: 1200px; height: 1200px; overflow: hidden; }
  body {
    background: var(--backdrop);
    font-family: "Tinos", "Times New Roman", serif;
    position: relative;
  }
  .card {
    position: absolute;
    left: 150px;
    width: 900px;
    height: 514px;
    overflow: hidden;
  }
  .card--front { top: 56px; background: var(--brand-blue); }
  .card--back { top: 630px; background: var(--paper); }

  .brand {
    position: absolute;
    display: flex;
    align-items: center;
    gap: 16px;
    font-size: 50px;
    line-height: 1;
    white-space: nowrap;
  }
  .brand__dot { width: 22px; height: 22px; border-radius: 50%; flex: none; }
  .card--front .brand { left: 0; right: 0; top: 180px; justify-content: center; color: var(--paper); }
  .card--front .brand__dot { background: var(--brand-red); }
  .front__company {
    position: absolute;
    right: 48px;
    bottom: 48px;
    color: var(--paper);
    font-size: 38px;
  }

  .person { position: absolute; right: 90px; top: 54px; text-align: left; }
  .person__name { color: var(--brand-blue); font-size: 46px; line-height: 1.05; }
  .person__title { color: var(--ink); font-size: 24px; margin-left: 36px; }

  .card--back .brand { left: 60px; top: 200px; color: var(--brand-blue); font-size: 40px; }
  .card--back .brand__dot { background: var(--brand-blue); width: 18px; height: 18px; }

  .address {
    position: absolute;
    left: 60px;
    top: 268px;
    color: var(--address-red);
    font-size: 24px;
  }
  .contacts {
    position: absolute;
    left: 300px;
    top: 318px;
    list-style: none;
    color: var(--ink);
    font-size: 23px;
    line-height: 1.25;
  }
  .contacts li { display: flex; align-items: flex-start; gap: 14px; margin-bottom: 6px; }
  .contacts svg { flex: none; width: 26px; height: 26px; margin-top: 2px; }

  .stripe {
    position: absolute;
    right: 0;
    bottom: 0;
    display: flex;
  }
  .stripe span { width: 78px; height: 30px; }
  .stripe .is-red { background: var(--brand-red); }
  .stripe .is-blue { background: var(--brand-blue); }
</style>
</head>
<body>
  <section class="card card--front" aria-label="Card front">
    <div class="brand"><span class="brand__dot"></span>Bramblecourt Holdings</div>
    <p class="front__company">Bramblecourt Holdings Australia Pty Ltd</p>
  </section>

  <section class="card card--back" aria-label="Card back">
    <div class="person">
      <p class="person__name">Daniel Okafor</p>
      <p class="person__title">Managing Director</p>
    </div>

    <div class="brand"><span class="brand__dot"></span>Bramblecourt Holdings</div>
    <p class="address">14 Wattlebird Close, Tarneit VIC 3029</p>

    <ul class="contacts">
      <li>
        <svg viewBox="0 0 26 26" aria-hidden="true"><rect width="26" height="26" rx="5" fill="var(--icon-blue)"/><path d="M8 6c1 0 2 2.5 2 3s-1.2 1-1 2c.5 2 2.5 4 4.5 4.5 1 .2 1.5-1 2-1s3 1 3 2-1.5 2.5-3 2.5C10 19 7 16 6.5 10 6.5 8 7 6 8 6z" fill="#fff"/></svg>
        <span>+61 3 9000 1234 (Telephone)<br>0400 555 218 (Mobile)</span>
      </li>
      <li>
        <svg viewBox="0 0 26 26" aria-hidden="true"><rect x="1" y="5" width="24" height="16" fill="var(--icon-blue)"/><path d="M1 5l12 9 12-9" fill="none" stroke="#fff" stroke-width="1.6"/></svg>
        <span>d.okafor.mail@example.com</span>
      </li>
      <li>
        <svg viewBox="0 0 26 26" aria-hidden="true"><g fill="none" stroke="var(--icon-blue)" stroke-width="1.6"><circle cx="13" cy="13" r="11"/><ellipse cx="13" cy="13" rx="5" ry="11"/><path d="M2 13h22M4 7h18M4 19h18"/></g></svg>
        <span>daniel@bramblecourt.com.au</span>
      </li>
    </ul>

    <div class="stripe" aria-hidden="true">
      <span class="is-red"></span><span class="is-blue"></span><span class="is-red"></span><span class="is-blue"></span>
    </div>
  </section>
</body>
</html>
```